Personal Injury Lawyer Billboard

I would like a design created featuring the image of the lawyer centered in the middle of the design.
To the left of the lawyer's image it should read "INJURED?"
To the right of the lawyer's image, it should read "CALL DEAN!"
Under Call Dean, include the phone number 318-555-0187.
At the bottom of the design include the lawyers information "Dean Marlowe Accident & Injury Lawyers"
PLEASE REMOVED THE BACKGROUND IMAGERY OF THE PHOTO SUBMITTED. Also, the colors for this design should match the colors shown in the logo (navy, white and relective soft gold). Please use those color combinations in ways that best stand out.

```html
<!DOCTYPE html>
<html lang="en">
<head>
<meta charset="UTF-8">
<title>Dean Marlowe Accident &amp; Injury Lawyers – Billboard</title>
<link href="https://fonts.googleapis.com/css2?family=Bebas+Neue&family=Libre+Baskerville:wght@700&display=swap" rel="stylesheet">
<style>
  :root {
    --navy: #0f1a45;
    --navy-deep: #08102f;
    --navy-soft: #242c5c;
    --white: #ffffff;
    --gold: #dcc35a;
    --gold-warm: #e3a22a;
    --gold-pale: #d6cf7a;
    --page: #e4e4e4;
  }
  * { margin: 0; padding: 0; box-sizing: border-box; }
  html, body {
    width: 1091px;
    height: 1200px;
    overflow: hidden;
    background: var(--page);
  }
  .billboard {
    position: absolute;
    left: 30px;
    top: 430px;
    width: 1031px;
    height: 340px;
    background: var(--navy);
    overflow: hidden;
    box-shadow: 0 10px 28px rgba(0, 0, 0, 0.35);
    font-family: "Bebas Neue", "Arial Narrow", sans-serif;
  }
  .billboard__panel {
    position: absolute;
    left: 0;
    top: 0;
    width: 1031px;
    height: 273px;
  }
  .lawyer-photo {
    position: absolute;
    left: 448px;
    top: 18px;
    width: 190px;
    height: 255px;
    border-radius: 95px 95px 0 0;
    background: linear-gradient(180deg, #8a6a55 0%, #6b5048 30%, #1d2656 55%, #141d4a 100%);
    z-index: 1;
  }
  .headline-injured {
    position: absolute;
    left: 27px;
    top: 28px;
    font-size: 150px;
    font-weight: 400;
    line-height: 1;
    white-space: nowrap;
    isolation: isolate;
    z-index: 2;
  }
  .headline-injured__fill {
    background: linear-gradient(180deg, var(--gold-pale) 0%, var(--gold-warm) 100%);
    -webkit-background-clip: text;
    background-clip: text;
    color: transparent;
  }
  .headline-injured::before {
    content: attr(data-text);
    position: absolute;
    left: -6px;
    top: 5px;
    color: var(--navy-deep);
    z-index: -1;
  }
  .firm-name {
    position: absolute;
    left: 43px;
    top: 168px;
    color: var(--white);
    line-height: 1;
    white-space: nowrap;
    z-index: 2;
  }
  .firm-name__main { display: block; font-size: 54px; letter-spacing: 0.5px; }
  .firm-name__sub { display: block; font-size: 27px; letter-spacing: 0.3px; margin-top: 8px; }
  .headline-call {
    position: absolute;
    left: 638px;
    top: 34px;
    font-size: 105px;
    font-weight: 400;
    line-height: 1;
    color: var(--white);
    white-space: nowrap;
    z-index: 2;
  }
  .headline-call__name { color: var(--gold); }
  .phone {
    position: absolute;
    left: 638px;
    top: 131px;
    font-size: 80px;
    line-height: 1;
    color: var(--gold);
    white-space: nowrap;
    z-index: 2;
  }
  .website-bar {
    position: absolute;
    left: 635px;
    top: 221px;
    width: 396px;
    height: 52px;
    background: var(--white);
    display: flex;
    align-items: center;
    justify-content: flex-end;
    padding-right: 38px;
    z-index: 2;
  }
  .website {
    font-size: 33px;
    letter-spacing: 3px;
    color: var(--navy);
    white-space: nowrap;
  }
  .firm-band {
    position: absolute;
    left: 0;
    top: 273px;
    width: 1031px;
    height: 67px;
    background: linear-gradient(90deg, var(--gold-warm) 0%, var(--gold) 100%);
    display: flex;
    align-items: center;
    justify-content: center;
    z-index: 2;
  }
  .firm-band__text {
    font-family: "Libre Baskerville", Georgia, serif;
    font-weight: 700;
    font-size: 30px;
    letter-spacing: 2.5px;
    color: var(--navy);
    white-space: nowrap;
  }
</style>
</head>
<body>
  <main class="billboard">
    <svg class="billboard__panel" viewBox="0 0 1031 273" aria-hidden="true">
      <polygon points="372,0 1031,0 1031,273 560,273" fill="var(--navy-soft)" opacity="0.55"/>
    </svg>

    <div class="lawyer-photo" role="img" aria-label="Portrait of the lawyer in a navy suit and green tie, smiling with a raised fist"></div>

    <h1 class="headline-injured" data-text="INJURED?"><span class="headline-injured__fill">INJURED?</span></h1>

    <p class="firm-name">
      <span class="firm-name__main">DEAN MARLOWE</span>
      <span class="firm-name__sub">ACCIDENT &amp; INJURY LAWYERS</span>
    </p>

    <h2 class="headline-call">CALL <span class="headline-call__name">DEAN!</span></h2>
    <p class="phone">318-555-0187</p>

    <div class="website-bar">
      <p class="website">WWW.DEANMARLOWE.COM</p>
    </div>

    <footer class="firm-band">
      <p class="firm-band__text">DEAN MARLOWE ACCIDENT &amp; INJURY LAWYERS</p>
    </footer>
  </main>
</body>
</html>
```